Social Media App Needs PPT Template

We need a PowerPoint template for a new social media company based in the DC area called "Bold Ledger." We provide an interactive digital platform for executives to share actionable advice. We would like to see designs that use our orange logo color as an accent, but are mainly grey, white, and black. The final design should communicate clean, chic, modern, and professional.

Target Market(s)

Executives

Industry/Entity Type

Information Technology

Font styles to use
Sans Serif

Colors
f78f20
fbe7d2
ffffff
000000
e8e8e8
757575

Requirements
Must have
• My project must have title page and many options for the body of the ppt (graphs, tables, etc). It also needs to be easy to modify. I must have someone who is experienced in creating powerpoint templates.
Nice to have
• It would be nice to have a very modern and clean design that includes the logo on every page, but still leaves a lot of room for the content of the slide
Should not have
• My design project should not look to busy.

```html
<!DOCTYPE html>
<html lang="en">
<head>
<meta charset="utf-8">
<title>Bold Ledger – About Our Company</title>
<link href="https://fonts.googleapis.com/css2?family=Lato:ital,wght@0,300;0,400;0,700;1,700&display=swap" rel="stylesheet">
<style>
  :root {
    --board: #929292;
    --paper: #f7f7f7;
    --orange: #e8861a;
    --orange-light: #ef9a2c;
    --black: #000000;
    --ink: #4a4a4a;
    --placeholder: #cbcccd;
    --white: #ffffff;
  }
  html, body {
    margin: 0;
    padding: 0;
    width: 1200px;
    height: 960px;
    overflow: hidden;
    background: var(--board);
    font-family: "Lato", sans-serif;
  }
  .page-label {
    position: absolute;
    top: 44px;
    left: 0;
    width: 1200px;
    text-align: center;
    color: var(--white);
    font-weight: 300;
    font-size: 24px;
    margin: 0;
  }
  .slide {
    position: absolute;
    left: 68px;
    top: 106px;
    width: 1062px;
    height: 797px;
    background: radial-gradient(ellipse at 40% 25%, #ffffff 0%, var(--paper) 60%, #f1f1f1 100%);
    overflow: hidden;
  }
  .slide-graphics {
    position: absolute;
    left: 0;
    top: 0;
    width: 1062px;
    height: 797px;
  }
  .slide-title {
    position: absolute;
    left: 32px;
    top: 68px;
    margin: 0;
    color: var(--white);
    font-weight: 300;
    font-size: 41px;
    letter-spacing: 0.2px;
  }
  .brand {
    position: absolute;
    left: 865px;
    top: 86px;
    display: flex;
    align-items: center;
    gap: 8px;
    color: var(--white);
    font-weight: 700;
    font-size: 22px;
  }
  .brand-dot {
    width: 14px;
    height: 14px;
    border-radius: 50%;
    background: var(--orange);
  }
  .column {
    position: absolute;
    top: 222px;
    width: 474px;
    color: var(--ink);
    font-size: 16px;
    line-height: 21.2px;
    text-align: justify;
  }
  .column p { margin: 0 0 21px; }
  .column-left { left: 38px; }
  .column-right { left: 556px; width: 458px; }
  .lead {
    color: var(--orange);
    font-weight: 700;
    font-style: italic;
    font-size: 18.6px;
    line-height: 23px;
  }
  .column-left .lead { margin-bottom: 27px; }
  .image-slot {
    position: absolute;
    left: 558px;
    top: 388px;
    width: 454px;
    height: 285px;
    background: var(--placeholder);
    display: flex;
    align-items: center;
    justify-content: center;
    color: #dfe0e1;
    font-weight: 300;
    font-size: 33px;
  }
  .footer-text {
    position: absolute;
    left: 29px;
    top: 760px;
    color: var(--white);
    font-size: 14px;
  }
  .footer-text .sep { margin: 0 6px; }
</style>
</head>
<body>
  <p class="page-label">Page 3</p>

  <section class="slide">
    <svg class="slide-graphics" viewBox="0 0 1062 797" aria-hidden="true">
      <!-- header -->
      <polygon points="816,35 1062,35 1062,46 805,46" fill="var(--orange)"/>
      <polygon points="0,50 808,50 724,134 0,134" fill="var(--orange)"/>
      <polygon points="640,50 808,50 724,134 640,134" fill="var(--orange-light)" opacity="0.6"/>
      <polygon points="0,110 760,105 736,134 0,134" fill="var(--orange-light)" opacity="0.5"/>
      <polygon points="816,50 1062,50 1062,134 732,134" fill="var(--black)"/>
      <polygon points="0,138 716,138 706,148 0,148" fill="var(--black)"/>
      <!-- footer -->
      <polygon points="0,754 304,754 272,785 0,785" fill="var(--black)"/>
      <polygon points="309,754 1062,754 1062,785 278,785" fill="var(--orange)"/>
    </svg>

    <h1 class="slide-title">About Our Company</h1>

    <div class="brand"><span class="brand-dot"></span><span>Bold Ledger</span></div>

    <div class="column column-left">
      <p class="lead">Lorem ipsum dolor sit amet, consectetuer adipiscing elit, sed diam nonummy nibh euismod tincidunt ut laoreet dolore magna aliquam erat volutpat. Ut wisi enim ad minim veniam, quis nostrud exerci tation ullamcorper suscipit lobortis nisl ut aliquip ex ea commodo consequat.</p>
      <p>Duis autem vel eum iriure dolor in hendrerit in vulputate velit esse molestie consequat, vel illum dolore eu feugiat nulla facilisis at vero eros et accumsan et iusto odio dignissim qui blandit praesent luptatum zzril delenit augue duis dolore te feugait nulla facilisi. Nam liber tempor cum soluta nobis eleifend option congue nihil imperdiet doming id quod mazim placerat facer possim assum. Typi non habent claritatem insitam; est usus legentis in iis qui facit eorum claritatem. Investigationes demonstraverunt lectores legere me lius quod ii legunt saepius. Claritas est etiam processus dynamicus, qui sequitur mutationem consuetudium lectorum.</p>
      <p style="text-align:left">Typi non habent claritatem insitam; est usus legentis in iis qui facit eorum claritatem. Investigationes.</p>
    </div>

    <div class="column column-right">
      <p>Duis autem vel eum iriure dolor in hendrerit in vulputate velit esse molestie consequat, vel illum dolore eu feugiat nulla facilisis at vero eros et accumsan et iusto odio dignissim qui blandit praesent luptatum zzril delenit augue duis dolore te feugait nulla facilisi. Nam liber tempor cum soluta nobis eleifend option congue nihil imperdiet doming id quod mazim placerat facer possim assum.</p>
    </div>

    <div class="image-slot" role="img" aria-label="Placeholder area for a company photograph">Image Goes Here</div>

    <div class="footer-text">www.boldledger.com<span class="sep">|</span>Page 1</div>
  </section>
</body>
</html>
```